Bulldog themed background for Real Estate Purchase Letter

I need a phantom background or watermark on a standard 8 1/2" x 11" paper. I am going to put a letter over the background. I want a bulldog theme that is cute, funny and original. This letter is for a real estate project and we want to capture the person sub-consciously . Attached is my personal dogs. If you want to use them you can but not required. I have attached the letter that I am trying to emulate. I want bulldogs not horses.

Target Market(s)

45 years old and higher

Industry/Entity Type

Real Estate

Font styles to use
Serif
Sans Serif

Colors

Designer to choose colors to be used in the design.

Requirements
Must have
• fun, happiness, reassuring,
Should not have
• violence, negativity, unhappy

```html
<!DOCTYPE html>
<html lang="en">
<head>
<meta charset="utf-8">
<title>Home Closing Thank-You Letter</title>
<link rel="stylesheet" href="https://fonts.googleapis.com/css2?family=Tinos&display=swap">
<style>
  :root {
    --backdrop: #141414;
    --paper: #ffffff;
    --ink: #2a2a2a;
    --grass-light: #cfe0c4;
    --grass-mid: #8fb578;
    --grass-deep: #5f8f4c;
    --dog-shadow: rgba(120, 120, 120, 0.18);
  }
  html, body {
    margin: 0;
    padding: 0;
    width: 960px;
    height: 1200px;
    overflow: hidden;
    background: var(--backdrop);
  }
  .letter-page {
    position: absolute;
    left: 30px;
    top: 17px;
    width: 900px;
    height: 1165px;
    background: var(--paper);
    overflow: hidden;
    font-family: "Tinos", "Times New Roman", serif;
    font-size: 18px;
    line-height: 24px;
    letter-spacing: -0.45px;
    color: var(--ink);
  }
  .background-scene {
    position: absolute;
    left: 0;
    right: 0;
    bottom: 0;
    height: 620px;
    background:
      radial-gradient(ellipse 260px 300px at 62% 38%, var(--dog-shadow), transparent 70%),
      linear-gradient(to bottom, rgba(255,255,255,0) 0%, rgba(255,255,255,0) 50%, var(--grass-light) 68%, var(--grass-mid) 86%, var(--grass-deep) 100%);
  }
  .letter-block {
    position: absolute;
    left: 73px;
    width: 740px;
    margin: 0;
  }
  .date-line { top: 106px; }
  .recipient { top: 154px; }
  .salutation { top: 251px; }
  .greeting { top: 300px; }
  .para-thanks { top: 348px; }
  .para-evaluation { top: 492px; }
  .para-closing { top: 612px; }
  .sign-off { top: 708px; }
  .signature { top: 804px; }
</style>
</head>
<body>
  <main class="letter-page">
    <div class="background-scene" role="img" aria-label="Faded photo of two friendly bulldogs wearing bandanas standing on a grassy lawn"></div>

    <p class="letter-block date-line">Date</p>
    <p class="letter-block recipient">Member Name(s)<br>Address<br>City/State/Zip Code</p>
    <p class="letter-block salutation">Dear Name(s):</p>
    <p class="letter-block greeting">Congratulations on the closing of your home!</p>

    <p class="letter-block para-thanks">The Harbor Crest HomeStride program would like to take this opportunity to say thank you for allowing our team to assist you with your real estate needs.&nbsp; Our team’s goal was to make your real estate experience as smooth and pleasurable as possible.&nbsp; All members of your real estate team (your Real Estate Agent, and your Harbor Crest Specialist) worked together to ensure that you received the excellent service you are accustomed to from Harbor Crest.&nbsp; We sincerely hope that we were successful!</p>

    <p class="letter-block para-evaluation">In the next few days, you will receive a service evaluation from the Harbor Crest Savings Bank.&nbsp; This is our program’s report card.&nbsp; We are very anxious to hear about your experience using the HomeStride program.&nbsp; Your feedback is extremely valuable!&nbsp; We respectfully request that you take a moment to fill out the evaluation and return it to Harbor Crest.</p>

    <p class="letter-block para-closing">Again, on behalf of the entire HomeStride team, thank you for using the program and selecting (insert real estate firm name).&nbsp; We hope that HomeStride will again be able to serve you with your future real estate needs.</p>

    <p class="letter-block sign-off">Sincerely,</p>
    <p class="letter-block signature">(Insert Principal Name)<br>(Insert Title)</p>
  </main>
</body>
</html>
```